Business card for medical clinic

I need an upmarket, modern medical/health business card for my clinic

Contact Information for Business Card

name, address, email, qr code

```html
<!DOCTYPE html>
<html lang="en">
<head>
<meta charset="utf-8">
<title>Kestrel Health Group – Business Card</title>
<link rel="stylesheet" href="https://fonts.googleapis.com/css2?family=Montserrat:wght@300;400;600;700&display=swap">
<style>
  :root {
    --stage: #2b2c2f;
    --sky: #29abe2;
    --ocean: #1b75b0;
    --navy: #123f6b;
    --ink: #1c1c1e;
    --paper: #ffffff;
    --slate: #4a4a4a;
    --mist: #e8eef3;
  }
  * { box-sizing: border-box; margin: 0; padding: 0; }
  html, body {
    width: 1200px; height: 880px; overflow: hidden;
    background: var(--stage);
    font-family: "Montserrat", Arial, sans-serif;
  }
  .sheet {
    position: relative; width: 1200px; height: 880px;
    display: flex; align-items: center; justify-content: center; gap: 40px;
  }
  .card {
    position: relative; width: 540px; height: 310px;
    border-radius: 18px; overflow: hidden;
    box-shadow: 0 14px 30px rgba(0,0,0,.45);
  }

  /* Back */
  .card-back {
    background: linear-gradient(160deg, var(--sky) 0%, #1f8fcb 45%, var(--ocean) 80%, #1a5f93 100%);
    display: flex; align-items: center; justify-content: center; gap: 18px;
  }
  .back-mark {
    width: 58px; height: 58px; border-radius: 50%;
    border: 4px solid var(--navy);
  }
  .back-name {
    font-weight: 600; font-size: 28px; letter-spacing: 2px;
    color: var(--navy); text-transform: uppercase; line-height: 1.15;
  }

  /* Front */
  .card-front { background: var(--paper); }
  .card-front .waves { position: absolute; inset: 0; }
  .brand {
    position: absolute; top: 36px; right: 34px;
    display: flex; align-items: center; gap: 12px;
  }
  .brand-mark {
    width: 40px; height: 40px; border-radius: 50%;
    border: 3px solid var(--ocean);
  }
  .brand-name {
    font-weight: 600; font-size: 17px; letter-spacing: 1.5px;
    color: var(--ocean); text-transform: uppercase; line-height: 1.2;
  }
  .accent-bar {
    position: absolute; left: 0; top: 92px; width: 8px; height: 48px;
    background: var(--sky);
  }
  .person { position: absolute; left: 28px; top: 92px; }
  .person-name {
    font-weight: 700; font-size: 23px; letter-spacing: .5px;
    color: var(--sky); text-transform: uppercase;
  }
  .person-role { font-weight: 400; font-size: 14px; color: var(--slate); margin-top: 2px; }

  .contact {
    position: absolute; left: 40px; top: 200px;
    color: var(--paper); font-weight: 300; font-size: 12.5px; line-height: 15px;
  }
  .address { margin-bottom: 7px; }
  .contact-list { list-style: none; }
  .contact-list li { display: flex; align-items: center; gap: 8px; }
  .contact-list svg { width: 12px; height: 12px; flex: none; }
</style>
</head>
<body>
<main class="sheet">

  <section class="card card-back" aria-label="Card back">
    <span class="back-mark"></span>
    <span class="back-name">Kestrel Health<br>Group</span>
  </section>

  <section class="card card-front" aria-label="Card front">
    <svg class="waves" viewBox="0 0 540 310" aria-hidden="true">
      <path d="M0,160 C110,125 220,118 320,128 C420,138 480,98 540,45 V310 H0 Z" fill="var(--sky)" opacity=".35"/>
      <path d="M0,172 C110,137 220,130 320,140 C420,150 480,110 540,58 V310 H0 Z" fill="var(--ocean)"/>
      <path d="M0,185 C110,150 220,142 320,150 C420,158 480,120 540,70 V310 H0 Z" fill="var(--paper)"/>
      <path d="M0,192 C110,157 220,149 320,157 C420,165 480,127 540,77 V310 H0 Z" fill="var(--ink)"/>
    </svg>

    <div class="brand">
      <span class="brand-mark"></span>
      <span class="brand-name">Kestrel Health<br>Group</span>
    </div>

    <span class="accent-bar"></span>
    <div class="person">
      <p class="person-name">Daniel Hart</p>
      <p class="person-role">Managing Director</p>
    </div>

    <div class="contact">
      <p class="address">Your address, City<br>State, Zip 1234</p>
      <ul class="contact-list">
        <li><svg viewBox="0 0 12 12"><path d="M3 1 L5 3.5 L4 4.8 Q5 7 7.2 8 L8.5 7 L11 9 L9.5 11 Q4 10.5 1 3 Z" fill="var(--sky)"/></svg>123 456 789</li>
        <li><svg viewBox="0 0 12 12"><rect x="3" y="0.5" width="6" height="11" rx="1.2" fill="none" stroke="var(--sky)" stroke-width="1.2"/><circle cx="6" cy="9.5" r=".7" fill="var(--sky)"/></svg>123 456 789</li>
        <li><svg viewBox="0 0 12 12"><rect x="0.6" y="2.5" width="10.8" height="7.5" rx="1" fill="none" stroke="var(--sky)" stroke-width="1.2"/><path d="M1 3 L6 7 L11 3" fill="none" stroke="var(--sky)" stroke-width="1.2"/></svg>info@kestrelhealth.com</li>
        <li><svg viewBox="0 0 12 12"><circle cx="6" cy="6" r="5.2" fill="none" stroke="var(--sky)" stroke-width="1.2"/><ellipse cx="6" cy="6" rx="2.2" ry="5.2" fill="none" stroke="var(--sky)" stroke-width="1"/><path d="M1 6 H11" stroke="var(--sky)" stroke-width="1"/></svg>www.kestrelhealth.com</li>
      </ul>
    </div>
  </section>

</main>
</body>
</html>
```